Brightmoor Essentials colloidal silver spray for pets.

We need a label for an 8-oz cobalt blue spray bottle. We are a small company just starting to share the benefits of colloidal silver. Our first offering will be the 8-oz spray bottle for pets. We would also like to update our logo. The finished project should be crisp and incorporate a dog on the label. I have attached the information we would like on the label and our logo, which can be changed to match your vision.
Updates

Hi, I would like to remind you that we are using a cobalt blue bottle with a black sprayer and would like an updated logo. Also, for the business cards, we don't want an animal on them, as we are planning future products for people. thank you

```html
<!DOCTYPE html>
<html lang="en">
<head>
<meta charset="utf-8">
<title>Brightmoor Essentials – Colloidal Silver Pet Spray Label</title>
<link rel="stylesheet" href="https://fonts.googleapis.com/css2?family=Quicksand:wght@400;500;600;700&family=Lora:ital,wght@1,400&display=swap">
<style>
  :root {
    --page-bg: #c8c8c8;
    --label-white: #f4f5f4;
    --navy: #2e3675;
    --green: #5aa54f;
    --green-dark: #3f8a3a;
    --green-light: #8fc285;
    --photo-tan: #b07a52;
    --photo-cream: #efe6dc;
  }
  * { margin: 0; padding: 0; box-sizing: border-box; }
  html, body {
    width: 741px; height: 1200px; overflow: hidden;
    background: var(--page-bg);
  }
  .canvas { position: relative; width: 741px; height: 1200px; }
  .label {
    position: absolute; left: 20px; top: 210px;
    width: 701px; height: 780px;
    background: var(--label-white);
    overflow: hidden;
    font-family: "Quicksand", sans-serif;
    color: var(--navy);
  }
  .frame { position: absolute; inset: 0; }
  .leaves {
    position: absolute;
    background: radial-gradient(ellipse at center, rgba(90,165,79,0.35), rgba(90,165,79,0) 70%);
  }
  .leaves--top { left: 113px; top: 80px; width: 150px; height: 124px; }
  .leaves--bottom { left: 400px; top: 420px; width: 230px; height: 280px; }
  .brand {
    position: absolute; left: 0; right: 0; top: 205px;
    text-align: center;
    font-weight: 500; font-size: 30px; letter-spacing: 1px;
    color: var(--navy);
  }
  .product-name {
    position: absolute; left: 0; right: 0; top: 288px;
    text-align: center;
    font-weight: 500; font-size: 76px; line-height: 78px;
    letter-spacing: 1px; color: var(--navy);
  }
  .tagline {
    position: absolute; left: 0; right: 0; top: 455px;
    text-align: center;
    font-family: "Lora", serif; font-style: italic;
    font-size: 29px; color: var(--green);
  }
  .features {
    position: absolute; left: 297px; top: 524px;
    list-style: none; font-size: 17px; line-height: 28px;
    color: var(--navy);
  }
  .features li::before {
    content: ""; display: inline-block;
    width: 5px; height: 5px; border-radius: 50%;
    background: var(--green); margin-right: 9px; vertical-align: middle;
  }
  .pet-photo {
    position: absolute; left: 87px; top: 508px; width: 198px; height: 216px;
    background: linear-gradient(160deg, var(--photo-tan) 0%, #c99b73 45%, var(--photo-cream) 100%);
    border-radius: 90px 90px 0 0;
  }
  .net-band {
    position: absolute; left: 0; right: 0; top: 724px; height: 56px;
    background: linear-gradient(90deg, var(--green-light), var(--green) 55%, var(--green-dark));
    display: flex; align-items: center; justify-content: center;
    color: #fff; font-weight: 700; font-size: 18px;
  }
</style>
</head>
<body>
<div class="canvas">
  <section class="label">
    <svg class="frame" width="701" height="780" viewBox="0 0 701 780" aria-hidden="true">
      <!-- navy arc frame -->
      <path d="M 272 72 A 283 283 0 0 1 610 265" fill="none" stroke="var(--navy)" stroke-width="3" stroke-linecap="round"/>
      <path d="M 110 280 A 283 283 0 0 0 170 610" fill="none" stroke="var(--navy)" stroke-width="3" stroke-linecap="round"/>
      <path d="M 190 625 A 283 283 0 0 0 400 640" fill="none" stroke="var(--navy)" stroke-width="3" stroke-linecap="round"/>
      <!-- dotted accents -->
      <path d="M 300 90 A 265 265 0 0 1 560 210" fill="none" stroke="var(--green)" stroke-width="6" stroke-linecap="round" stroke-dasharray="0 16"/>
      <path d="M 135 335 A 265 265 0 0 0 225 600" fill="none" stroke="var(--green)" stroke-width="5" stroke-linecap="round" stroke-dasharray="0 15"/>
    </svg>
    <div class="leaves leaves--top" role="img" aria-label="Green leafy sprig decoration"></div>
    <div class="leaves leaves--bottom" role="img" aria-label="Green leafy branch decoration"></div>

    <div class="brand">Brightmoor Essentials</div>
    <h1 class="product-name">COLLOIDAL<br>SILVER</h1>
    <p class="tagline">Natural First Aid for Pets</p>

    <div class="pet-photo" role="img" aria-label="Photo of a brown and white dog looking up"></div>
    <ul class="features">
      <li>100% Pure</li>
      <li>No Preservatives</li>
      <li>No Additives</li>
    </ul>

    <div class="net-band">Net Weight: 250ml&nbsp;&nbsp;|&nbsp;&nbsp;8oz</div>
  </section>
</div>
</body>
</html>
```